Wine Label for a Sweet Wine Called "Glimmo"

We need a wine label that will be used for both a sweet red and a sweet white wine. The very important thing to remember is the target market for these wines is: young American women who love sweet wines and they also spend a lot of their money on their hair, clothes, jewelry, nails. They LOVE Glimmo (Glimmo is a word used to describe flashy accessories, jewelry, decoration.) This label needs to be eye catching, showy, fun, glittery. Please put the brand name, "Glimmo," big, and then in smaller but still readable words underneath the label or somewhere on the label: Sweet, Sophisticated, Red (or white). (An example of what I mean is attached). To differentiate between the two color wines you can suggest color changes to differentiate between the red label and the white label but the label design itself should be the same. Ultimately, the label can be the exact same label for both white and red as long as it looks good on a white wine (a greenish/yellow wine in a clear glass bottle) and a red wine (a dark color wine in a dark bottle).

I've attached an example of the text size relationship between the word Glimmo and the words to go underneath or elsewhere on the label, but you can certainly play with this-- it is just a suggestion of the text size relationship, and definitely NOT at all mandatory that you use any of these fonts.

You can pick the size of the label but try to stay within normal wine label sizes, meaning don't go bigger than approx. 3.5 inches wide and 5 inches tall.

Target Market(s)

Young American women who love sweet wines and spend a lot of money on their hair, clothes, jewelry, nails. They love Glimmo (Glimmo is a word that means flashy accessories, jewelry, decoration)

Requirements
Must have
• It needs to be flashy, glittery, fun, eye catching, memorable
Nice to have
• It shouldn't be too too ultra feminine! The target market is strong independent women and we also have men who will buy it too.

```html
<!DOCTYPE html>
<html lang="en">
<head>
<meta charset="utf-8">
<title>Glimmo – Sweet Wine Labels</title>
<link rel="stylesheet" href="https://fonts.googleapis.com/css2?family=Abril+Fatface&family=Montserrat:wght@300;400;700&display=swap">
<style>
  :root {
    --page-bg: #e6e1d8;
    --ink-white: #ffffff;
    --wash-teal: #2c9fb3;
    --wash-cream: #f3dca6;
    --wash-peach: #f0a27a;
    --wash-coral: #e8675e;
    --wash-crimson: #c8254a;
    --wash-rose: #e4869a;
  }

  * { box-sizing: border-box; margin: 0; padding: 0; }

  html, body {
    width: 1200px;
    height: 739px;
    overflow: hidden;
    background: var(--page-bg);
  }

  .label-sheet {
    position: relative;
    width: 1200px;
    height: 739px;
    display: flex;
    justify-content: space-around;
    align-items: center;
    padding: 0 80px;
  }

  .wine-label {
    position: relative;
    width: 370px;
    height: 560px;
    overflow: hidden;
    color: var(--ink-white);
    font-family: "Montserrat", sans-serif;
  }

  .label-artwork {
    position: absolute;
    inset: 0;
    background:
      radial-gradient(circle at 52% 50%, var(--wash-crimson) 0%, rgba(200,37,74,0.85) 14%, rgba(232,103,94,0.6) 32%, rgba(240,162,122,0) 55%),
      radial-gradient(circle at 30% 68%, rgba(228,134,154,0.7) 0%, rgba(228,134,154,0) 35%),
      radial-gradient(circle at 0% 0%, var(--wash-teal) 0%, rgba(44,159,179,0.55) 14%, rgba(44,159,179,0) 30%),
      radial-gradient(circle at 100% 100%, var(--wash-teal) 0%, rgba(44,159,179,0.6) 15%, rgba(44,159,179,0) 32%),
      radial-gradient(circle at 5% 100%, rgba(44,159,179,0.45) 0%, rgba(44,159,179,0) 22%),
      linear-gradient(160deg, var(--wash-cream) 0%, var(--wash-peach) 45%, var(--wash-coral) 75%, var(--wash-peach) 100%);
  }

  .brand-name {
    position: absolute;
    left: 0;
    right: 0;
    top: 180px;
    text-align: center;
    font-family: "Abril Fatface", serif;
    font-size: 96px;
    line-height: 1;
    letter-spacing: -1px;
    color: var(--ink-white);
  }

  .tagline {
    position: absolute;
    left: 150px;
    top: 310px;
    list-style: none;
    font-size: 17px;
    line-height: 1.45;
    letter-spacing: 1px;
  }

  .tagline .strong { font-weight: 700; }
  .tagline .regular { font-weight: 400; }
  .tagline .light { font-weight: 300; }

  .label-footer {
    position: absolute;
    left: 22px;
    right: 22px;
    bottom: 16px;
    display: flex;
    justify-content: space-between;
    font-size: 15px;
    font-weight: 700;
    letter-spacing: 1px;
  }
</style>
</head>
<body>
  <main class="label-sheet">
    <section class="wine-label wine-label--white">
      <div class="label-artwork" role="img" aria-label="Watercolour wash in teal, cream, peach and crimson with a sparkling glitter burst"></div>
      <h1 class="brand-name">Glimmo</h1>
      <ul class="tagline">
        <li class="strong">Sweet,</li>
        <li class="regular">Sophisticated,</li>
        <li class="strong">White,</li>
        <li class="light">and</li>
        <li class="strong">you</li>
      </ul>
      <footer class="label-footer">
        <span class="volume">75cl</span>
        <span class="abv">15%vol</span>
      </footer>
    </section>

    <section class="wine-label wine-label--red">
      <div class="label-artwork" role="img" aria-label="Watercolour wash in teal, cream, peach and crimson with a sparkling glitter burst"></div>
      <h1 class="brand-name">Glimmo</h1>
      <ul class="tagline">
        <li class="strong">Sweet,</li>
        <li class="regular">Sophisticated,</li>
        <li class="strong">Red,</li>
        <li class="light">and</li>
        <li class="strong">you</li>
      </ul>
      <footer class="label-footer">
        <span class="volume">75cl</span>
        <span class="abv">15%vol</span>
      </footer>
    </section>
  </main>
</body>
</html>
```